pet resort day care for our buisiness

we need a new web design for our pet center in Florida , we are provide the following services -
1. dog day car
2.dog/cat boarding
3. dog grooming
4. Dog training
5.pet food toy and clothing
our current websit is -http://www.tindlewoodpetcenter.com/
we are looking for a fresh new design that will reflect the change that we have made in the vusness from renovationnto the facelaty new management and new servises
Target Market(s)
Dog Lover , Upmarket
Industry/Entity Type
Pet
Number of Pages Required
5+ page
Font styles to use
Sans Serif
Requirements
Must have
- clean design , easy to understand and navigate , our target is the upmarket costumer how are dog lover
Should not have
- NOOO of the shelf design , confusing design , brown colors

```html
<!DOCTYPE html>
<html lang="en">
<head>
<meta charset="utf-8">
<title>Tindlewood Pet Center</title>
<link rel="stylesheet" href="https://fonts.googleapis.com/css2?family=Montserrat:wght@400;500;600&family=Open+Sans:ital,wght@0,400;0,600;1,400;1,600&display=swap">
<style>
:root{
  --pink:#e4466d;
  --pink-dark:#d23459;
  --green:#9cb84b;
  --ink:#333333;
  --text:#666666;
  --muted:#888888;
  --line:#dddddd;
  --soft:#f2f2f2;
  --footer:#3b3b3b;
  --footer-deep:#2a2a2a;
  --white:#ffffff;
}
*{box-sizing:border-box;margin:0;padding:0}
html,body{width:1200px;height:2256px;overflow:hidden}
body{position:relative;background:var(--white);font-family:"Open Sans",Arial,sans-serif;color:var(--text);border-top:4px solid #555b63}
.abs{position:absolute}
h1,h2,h3,h4{font-family:"Montserrat",Arial,sans-serif;font-weight:500;color:var(--ink)}
.accent{color:var(--green)}
.btn{position:absolute;display:flex;align-items:center;justify-content:center;color:var(--white);background:linear-gradient(var(--pink),var(--pink-dark));border-radius:3px;font-size:13px;text-transform:uppercase;letter-spacing:.3px;box-shadow:0 2px 3px rgba(0,0,0,.18)}
.btn.small{font-size:11px}

/* header */
.brand{left:92px;top:28px;display:flex;align-items:center;gap:14px}
.brand-dot{width:22px;height:22px;border-radius:50%;background:var(--green)}
.brand-name{font-family:"Montserrat",Arial,sans-serif;font-weight:600;font-size:25px;line-height:1.15;color:var(--green);width:170px}
.call{left:558px;top:70px;display:flex;align-items:center;gap:14px}
.call-icon{width:40px;height:40px;border:2px solid var(--green);border-radius:50%;display:flex;align-items:center;justify-content:center}
.call small{display:block;font-size:12px;color:var(--ink)}
.call strong{display:block;font-size:20px;font-weight:400;color:var(--pink);margin-top:2px}
.search{left:815px;top:70px;width:288px;height:38px;display:flex;border:1px solid var(--line);border-radius:2px}
.search span{flex:1;font-size:12px;color:var(--muted);padding:10px 14px}
.search i{width:42px;background:var(--pink);display:flex;align-items:center;justify-content:center}

/* navigation */
.nav{left:0;top:160px;width:1200px;height:48px;border-top:1px solid #cfcfcf;border-bottom:1px solid #cfcfcf;background:var(--white)}
.nav a{position:absolute;top:0;height:46px;line-height:46px;font-size:13px;color:var(--ink);text-decoration:none;text-transform:uppercase}
.nav .current{left:98px;width:110px;text-align:center;color:var(--white);z-index:1}
.nav .current::before{content:"";position:absolute;inset:0;background:var(--pink);transform:skewX(-16deg);z-index:-1}
.nav .sep{position:absolute;top:6px;width:1px;height:36px;background:#d5d5d5;transform:skewX(-16deg)}

/* hero */
.hero{left:0;top:208px;width:1200px;height:514px;background:linear-gradient(180deg,#8f7a66 0%,#7d6a58 20%,#6d8f3c 26%,#5f8a2c 60%,#4d7424 100%)}
.hero-photo{position:absolute;left:580px;top:0;width:360px;height:514px;background:radial-gradient(ellipse at 50% 55%,#f1e6cf 0%,#e2d2b2 45%,rgba(226,210,178,0) 72%)}
.hero h1{left:96px;top:152px;font-size:40px;color:var(--white);font-weight:500}
.hero p{left:100px;top:207px;width:470px;font-size:14px;line-height:22px;color:var(--white)}
.hero .btn{left:100px;top:293px;width:160px;height:50px}
.hero .arrow{top:228px}

/* welcome */
.video{left:99px;top:790px;width:407px;height:272px;background:linear-gradient(160deg,#9aa55c 0%,#6e8a3a 45%,#4f3b2e 75%,#3f5a26 100%);box-shadow:0 2px 5px rgba(0,0,0,.3)}
.play{position:absolute;left:182px;top:120px;width:42px;height:30px;border-radius:8px;background:#d4242a;display:flex;align-items:center;justify-content:center}
.welcome h2{left:544px;top:793px;font-size:32px}
.welcome .lead{left:546px;top:841px;width:570px;font-size:13px;line-height:22px;font-style:italic;font-weight:600;color:var(--ink)}
.welcome .body{left:546px;top:896px;width:560px;font-size:12.5px;line-height:24px;color:var(--muted)}
.welcome .btn{left:546px;top:1010px;width:160px;height:48px}

/* services */
.services{left:0;top:1122px;width:1200px;height:532px;background:var(--soft)}
.services h2{left:0;top:44px;width:1200px;text-align:center;font-size:31px}
.card{position:absolute;top:115px;width:316px;height:364px;background:var(--white);border:1px solid #e6e6e6}
.card .photo{position:absolute;left:6px;top:8px;width:302px;height:176px;border-radius:8px}
.card h3{position:absolute;left:14px;top:200px;font-size:17px;text-transform:uppercase}
.card p{position:absolute;left:14px;top:226px;width:290px;font-size:12.5px;line-height:21px;color:var(--muted)}
.card .btn{left:14px;top:303px;width:100px;height:37px}
.services .arrow{top:260px}

/* blog */
.blog h2{left:0;top:1680px;width:1200px;text-align:center;font-size:31px}
.post-photo{position:absolute;top:1746px;width:220px;height:166px;border:4px solid var(--white);box-shadow:0 3px 8px rgba(0,0,0,.35)}
.post h3{position:absolute;top:1750px;font-size:15px;text-transform:uppercase;font-weight:400}
.post .meta{position:absolute;top:1780px;font-size:11.5px;color:var(--ink);display:flex;gap:14px;align-items:center}
.post .meta span{display:flex;align-items:center;gap:6px}
.post p{position:absolute;top:1802px;width:280px;font-size:12.5px;line-height:21px;color:var(--ink)}
.post .btn{top:1873px;width:100px;height:37px}

/* footer */
.footer{left:0;top:1966px;width:1200px;height:242px;background:var(--footer);color:#e9e9e9}
.footer h4{position:absolute;top:42px;font-size:15px;color:var(--white);text-transform:uppercase;font-weight:600}
.footer .brand-f{position:absolute;left:120px;top:36px;display:flex;align-items:center;gap:10px}
.footer .brand-f .brand-dot{background:var(--white);width:16px;height:16px}
.footer .brand-f .brand-name{color:var(--white);font-size:18px;width:130px}
.footer .about{position:absolute;left:102px;top:120px;width:190px;font-size:13px;line-height:23px}
.footer .rule{position:absolute;top:30px;width:1px;height:200px;background:#4a4a4a}
.hours{position:absolute;left:330px;top:78px;font-size:12.5px;line-height:23px}
.hours .row{display:flex;gap:12px}
.contact{position:absolute;left:578px;top:76px;font-size:12.5px;line-height:20px}
.contact .row{display:flex;gap:12px;margin-bottom:12px;align-items:flex-start}
.contact .row svg{flex:none;margin-top:3px}
.contact .big{font-size:15px}
.news{position:absolute;left:882px;top:76px;width:220px;font-size:12.5px;line-height:20px}
.news .field{margin-top:14px;width:218px;height:32px;background:var(--white);border-radius:2px;color:#aaa;font-size:11px;padding:8px 12px}
.news .btn{position:relative;margin-top:8px;width:98px;height:34px;font-size:11px}
.bottom{left:0;top:2208px;width:1200px;height:48px;background:var(--footer-deep);color:#dcdcdc}
.bottom p{position:absolute;left:94px;top:16px;font-size:12px}
.social{position:absolute;left:920px;top:10px;display:flex;gap:12px}
.social span{width:28px;height:28px;border-radius:50%;background:#e6e6e6}
</style>
</head>
<body>

<header>
  <div class="abs brand">
    <span class="brand-dot"></span>
    <span class="brand-name">Tindlewood Pet Center</span>
  </div>
  <div class="abs call">
    <span class="call-icon">
      <svg width="18" height="18" viewBox="0 0 24 24"><path d="M6.6 10.8a15 15 0 0 0 6.6 6.6l2.2-2.2c.3-.3.7-.4 1-.2 1.1.4 2.3.6 3.6.6.6 0 1 .4 1 1V20c0 .6-.4 1-1 1A17 17 0 0 1 3 4c0-.6.4-1 1-1h3.5c.6 0 1 .4 1 1 0 1.3.2 2.5.6 3.6.1.3 0 .7-.2 1z" fill="#9cb84b"/></svg>
    </span>
    <div><small>Call Us Today!</small><strong>(954) 555-0147</strong></div>
  </div>
  <div class="abs search">
    <span>Enter your keywords...</span>
    <i><svg width="14" height="14" viewBox="0 0 24 24"><circle cx="10" cy="10" r="6.5" fill="none" stroke="#fff" stroke-width="3"/><path d="M15 15l6 6" stroke="#fff" stroke-width="3.5" stroke-linecap="round"/></svg></i>
  </div>
</header>

<nav class="abs nav">
  <a class="current" href="#">Home</a>
  <a href="#" style="left:237px">Boarding</a>
  <span class="sep" style="left:338px"></span>
  <a href="#" style="left:360px">Daycare</a>
  <span class="sep" style="left:438px"></span>
  <a href="#" style="left:466px">Grooming</a>
  <span class="sep" style="left:560px"></span>
  <a href="#" style="left:582px">Training</a>
  <span class="sep" style="left:663px"></span>
  <a href="#" style="left:685px">Boutique</a>
  <span class="sep" style="left:772px"></span>
  <a href="#" style="left:800px">Blog</a>
  <span class="sep" style="left:862px"></span>
  <a href="#" style="left:885px">Contact</a>
  <span class="sep" style="left:976px"></span>
  <a href="#" style="left:1000px">About Us</a>
</nav>

<section class="abs hero">
  <div class="hero-photo" role="img" aria-label="Labrador puppy running on a lawn with a tennis ball in its mouth"></div>
  <h1 class="abs">Life is Good</h1>
  <p class="abs">A pet paradise providing the best pet care in the greater Fort Lauderdale FL area. Professional cat &amp; dog boarding, doggy daycare, pet grooming, training, holistic foods &amp; pet boutique.</p>
  <a class="btn" href="#">View More Info</a>
  <svg class="abs arrow" style="left:42px" width="20" height="56" viewBox="0 0 20 56"><path d="M18 2L3 28l15 26" fill="none" stroke="#fff" stroke-width="2"/></svg>
  <svg class="abs arrow" style="left:1138px" width="20" height="56" viewBox="0 0 20 56"><path d="M2 2l15 26L2 54" fill="none" stroke="#fff" stroke-width="2"/></svg>
</section>

<section class="welcome">
  <div class="abs video" role="img" aria-label="Video tour: a dog resting on the grass in front of a garden shed">
    <span class="play"><svg width="14" height="16" viewBox="0 0 14 16"><path d="M1 1l12 7-12 7z" fill="#fff"/></svg></span>
  </div>
  <h2 class="abs">Welcome to <span class="accent">Tindlewood Pet Center</span></h2>
  <p class="abs lead">A pet paradise providing the best pet care in the greater Fort Lauderdale FL area. Professional cat &amp; dog boarding, doggy daycare, pet grooming, training, holistic foods &amp; pet boutique.</p>
  <p class="abs body">Discover how much Tindlewood has to offer for your pet boarding needs by viewing a virtual tour of our 16,000 s/f 'Home Away From Home'. See 9,000 s/f of air conditioned space and a 4,000 s/f out-door playground with a splash pool. Why not just come by and take a tour of our Fort Lauderdale FL retail store, grooming salon and air conditioned suites</p>
  <a class="btn" href="#">View More Info</a>
</section>

<section class="abs services">
  <h2 class="abs">We provide <span class="accent">these services</span></h2>
  <svg class="abs arrow" style="left:40px" width="12" height="22" viewBox="0 0 12 22"><path d="M10 2L2 11l8 9" fill="none" stroke="#999" stroke-width="2"/></svg>
  <svg class="abs arrow" style="left:1142px" width="12" height="22" viewBox="0 0 12 22"><path d="M2 2l8 9-8 9" fill="none" stroke="#999" stroke-width="2"/></svg>

  <article class="card" style="left:100px">
    <div class="photo" role="img" aria-label="Golden retriever sitting in the open back of a car" style="background:linear-gradient(135deg,#d9dde0,#b7a98a 55%,#8a8f92)"></div>
    <h3>Dog Day Car</h3>
    <p>It is a long established fact that a reader will be distracted by the readable content of a page when looking at its layout.</p>
    <a class="btn small" href="#">Read More</a>
  </article>
  <article class="card" style="left:441px">
    <div class="photo" role="img" aria-label="Dog and cat resting together" style="background:linear-gradient(135deg,#cfd3d6,#8a6a48 50%,#4a3a2e)"></div>
    <h3>Dog/Cat Boarding</h3>
    <p>It is a long established fact that a reader will be distracted by the readable content of a page when looking at its layout.</p>
    <a class="btn small" href="#">Read More</a>
  </article>
  <article class="card" style="left:785px">
    <div class="photo" role="img" aria-label="Small terrier wrapped in a towel after a bath" style="background:linear-gradient(135deg,#b89a86,#7d5a46 50%,#8e3a4e)"></div>
    <h3>Dog Grooming</h3>
    <p>It is a long established fact that a reader will be distracted by the readable content of a page when looking at its layout.</p>
    <a class="btn small" href="#">Read More</a>
  </article>
</section>

<section class="blog">
  <h2 class="abs">Latest <span class="accent">Blog</span></h2>

  <div class="post">
    <div class="post-photo" style="left:98px;background:linear-gradient(160deg,#9a5a45,#6f8a8a 50%,#c9c9c9)" role="img" aria-label="Staff member playing with dogs at the splash pool"></div>
    <h3 style="left:338px">The Best Place</h3>
    <div class="meta" style="left:338px">
      <span><svg width="11" height="11" viewBox="0 0 12 12"><rect x="1" y="2" width="10" height="9" fill="none" stroke="#555" stroke-width="1.4"/><path d="M1 5h10" stroke="#555" stroke-width="1.4"/></svg>September 23, 2014</span>
      <span><svg width="13" height="11" viewBox="0 0 14 12"><path d="M1 5c0-3 3-4 6-4s6 1 6 4-3 4-6 4l-4 2 1-3C2 7 1 6 1 5z" fill="#555"/></svg>10 comments</span>
    </div>
    <p style="left:338px">A pet paradise providing the best pet care in the greater Fort Lauderdale FL area. Professional cat &amp; dog boarding, doggy daycare</p>
    <a class="btn small" href="#" style="left:338px">Read More</a>
  </div>

  <div class="post">
    <div class="post-photo" style="left:620px;background:linear-gradient(160deg,#c9a34a,#7a6a5a 50%,#5a4a3e)" role="img" aria-label="Staff member holding two small dogs in the lobby"></div>
    <h3 style="left:860px">For Your Pets</h3>
    <div class="meta" style="left:860px">
      <span><svg width="11" height="11" viewBox="0 0 12 12"><rect x="1" y="2" width="10" height="9" fill="none" stroke="#555" stroke-width="1.4"/><path d="M1 5h10" stroke="#555" stroke-width="1.4"/></svg>September 23, 2014</span>
      <span><svg width="13" height="11" viewBox="0 0 14 12"><path d="M1 5c0-3 3-4 6-4s6 1 6 4-3 4-6 4l-4 2 1-3C2 7 1 6 1 5z" fill="#555"/></svg>10 comments</span>
    </div>
    <p style="left:860px">A pet paradise providing the best pet care in the greater Fort Lauderdale FL area. Professional cat &amp; dog boarding, doggy daycare</p>
    <a class="btn small" href="#" style="left:860px">Read More</a>
  </div>
</section>

<footer class="abs footer">
  <div class="brand-f">
    <span class="brand-dot"></span>
    <span class="brand-name">Tindlewood Pet Center</span>
  </div>
  <p class="about">Discover how much Tindlewood has to offer for your pet boarding needs by viewing a virtual tour of our 16,000 s/f 'Home Away</p>
  <span class="rule" style="left:312px"></span>

  <h4 style="left:330px">Open 7 days per week</h4>
  <div class="hours">
    <div class="row">
      <svg width="14" height="14" viewBox="0 0 14 14" style="margin-top:4px"><circle cx="7" cy="7" r="6" fill="none" stroke="#fff" stroke-width="1.6"/><path d="M7 3.5V7h2.5" fill="none" stroke="#fff" stroke-width="1.6"/></svg>
      <div>Monday – Saturday<br>7:00 am to 7:00 pm<br><span style="display:block;height:10px"></span>Sunday<br>9:00 am to 5:00 pm</div>
    </div>
  </div>
  <span class="rule" style="left:532px"></span>

  <h4 style="left:578px">Contact Details</h4>
  <div class="contact">
    <div class="row"><svg width="12" height="16" viewBox="0 0 12 16"><path d="M6 0a6 6 0 0 0-6 6c0 4.5 6 10 6 10s6-5.5 6-10a6 6 0 0 0-6-6zm0 8.5A2.5 2.5 0 1 1 6 3.5a2.5 2.5 0 0 1 0 5z" fill="#fff"/></svg><span>418 SE 12th Ave, Fort<br>Lauderdale, FL 33316</span></div>
    <div class="row big"><svg width="14" height="14" viewBox="0 0 24 24"><path d="M6.6 10.8a15 15 0 0 0 6.6 6.6l2.2-2.2c.3-.3.7-.4 1-.2 1.1.4 2.3.6 3.6.6.6 0 1 .4 1 1V20c0 .6-.4 1-1 1A17 17 0 0 1 3 4c0-.6.4-1 1-1h3.5c.6 0 1 .4 1 1 0 1.3.2 2.5.6 3.6.1.3 0 .7-.2 1z" fill="#fff"/></svg><span>954-555-0147</span></div>
    <div class="row"><svg width="14" height="11" viewBox="0 0 14 11"><rect x=".7" y=".7" width="12.6" height="9.6" fill="none" stroke="#fff" stroke-width="1.4"/><path d="M1 1l6 5 6-5" fill="none" stroke="#fff" stroke-width="1.4"/></svg><span>hello@tindlewoodpetcenter.com</span></div>
    <div class="row"><svg width="14" height="14" viewBox="0 0 14 14"><circle cx="7" cy="7" r="6.3" fill="#fff"/><path d="M1 7h12M7 1c-2.5 3-2.5 9 0 12M7 1c2.5 3 2.5 9 0 12" fill="none" stroke="#3b3b3b" stroke-width="1"/></svg><span>www.tindlewoodpetcenter.com</span></div>
  </div>
  <span class="rule" style="left:836px"></span>

  <h4 style="left:882px">Newsletter Signup</h4>
  <div class="news">
    Lorem ipsum dolor sit amet, consectetur adipiscing elit,
    <div class="field">Email address</div>
    <a class="btn" href="#">Subcribe</a>
  </div>
</footer>

<div class="abs bottom">
  <p>Copyright 2015 tindlewoodpetcenter. All Rights Reserved</p>
  <div class="social" aria-label="Social links">
    <span></span><span></span><span></span><span></span><span></span>
  </div>
</div>

</body>
</html>
```